Stationery Design Project for Nimbora, Chicago

Nimbora, a street parking application which helps car drivers find a street parking spot by offering an ideal path along which to look for parking. This path is calculated by our algorithm based on data (e.g. historical data, baseball games schedule, etc.). Along this path the driver will find a spot and will also save 70% of the search time. Customer we target is reg. between 21 and 45 yo.

We envision something young, fresh, bright and original. Slightly abstract maybe. It should represent the idea and elements of finding street parking in the city, e.g. car(s), parking spot, people, city, etc. (just ideas!).

Logo is attached.

Requirement:
- Business Cards (2 Sided Full Color CMYK)
- Letterhead (1 Sided Full Color CMYK)
- Envelope (1 Sided Full Color CMYK)
- Sticker (1 Sided Full Color CMYK), round with a 2inch diameter.

Reason: We're starting to get more and more designs and need more time to look into all of them. Very exciting!! Thanks to everybody!

Hi all, we're in the process of selecting our favs. Though choices!!! Really good submissions. Will keep you posted and sorry for the delay.

Target Market(s)

Car drivers and owners between 21 and 45

Industry/Entity Type

Parking

Requirements
Must have
• Sticker should be round and include company URL nimbora.com and the new logo which we will attach soon.
Should not have
• Should not be too serious or boring.

```html
<!DOCTYPE html>
<html lang="en">
<head>
<meta charset="utf-8">
<title>Nimbora Business Card</title>
<link rel="stylesheet" href="https://fonts.googleapis.com/css2?family=Open+Sans:wght@400;600;700&display=swap">
<style>
  :root {
    --backdrop: #d9d9db;
    --card-white: #ffffff;
    --ink: #1f1f1f;
    --ink-soft: #4a4a4a;
    --name-grey: #555555;
    --brand-blue: #1b6fc4;
    --brand-blue-deep: #1f3fae;
    --night: #050505;
    --night-edge: #5a5a5c;
    --lot-grey: #8d949c;
    --lot-asphalt: #6c7178;
  }
  * { box-sizing: border-box; margin: 0; padding: 0; }
  html, body { width: 1200px; height: 954px; overflow: hidden; }
  body {
    background: var(--backdrop);
    font-family: "Open Sans", Arial, sans-serif;
    position: relative;
  }
  .card {
    position: absolute;
    top: 77px;
    width: 456px;
    height: 795px;
    border-radius: 30px;
    overflow: hidden;
  }
  .card--front { left: 77px; background: var(--card-white); }
  .card--back {
    left: 632px;
    background: radial-gradient(ellipse 70% 55% at 50% 45%, var(--night) 55%, var(--night-edge) 100%);
  }
  .brand-dot {
    position: absolute;
    left: 50%;
    top: 53px;
    width: 148px;
    height: 148px;
    margin-left: -74px;
    border-radius: 50%;
    background: radial-gradient(circle at 40% 35%, #3d8fe6, var(--brand-blue-deep));
  }
  .wordmark {
    position: absolute;
    left: 0; right: 0;
    top: 210px;
    text-align: center;
    font-weight: 700;
    font-size: 82px;
    line-height: 1;
    letter-spacing: -1px;
  }
  .card--front .wordmark { color: var(--ink); }
  .card--back .wordmark { color: #ffffff; }
  .person {
    position: absolute;
    left: 50px;
    top: 340px;
    font-size: 25px;
    color: var(--ink-soft);
    white-space: nowrap;
  }
  .person__name { font-weight: 700; font-size: 35px; color: var(--name-grey); }
  .contact {
    position: absolute;
    left: 39px;
    top: 580px;
    list-style: none;
    font-size: 19px;
    line-height: 27px;
    color: var(--ink-soft);
  }
  .contact b { color: var(--ink); }
  .address {
    position: absolute;
    left: 39px;
    top: 712px;
    font-size: 19px;
    line-height: 27px;
    color: var(--ink-soft);
  }
  .corner-sweep { position: absolute; right: 0; bottom: 0; }
  .lot-photo {
    position: absolute;
    left: 0; right: 0; bottom: 0;
    height: 349px;
    background: linear-gradient(160deg, var(--lot-grey) 0%, #a9aeb4 30%, #b45a5a 55%, #6e7f96 75%, var(--lot-asphalt) 100%);
  }
  .back-url {
    position: absolute;
    left: 46px;
    bottom: 40px;
    font-size: 25px;
    color: #ffffff;
  }
</style>
</head>
<body>
  <section class="card card--front">
    <div class="brand-dot"></div>
    <div class="wordmark">nimbora</div>
    <p class="person"><span class="person__name">Your Name</span> | Designation</p>
    <ul class="contact">
      <li><b>p</b> : 123-456-7890</li>
      <li><b>c</b> : 123-456-7890</li>
      <li><b>e</b> : name@website.com</li>
      <li><b>w</b> : www.website.com</li>
    </ul>
    <p class="address">City Name, Street Name,<br>State Name, Country Code</p>
    <svg class="corner-sweep" width="200" height="260" viewBox="0 0 200 260">
      <defs>
        <linearGradient id="sweepFront" x1="0" y1="0" x2="0" y2="1">
          <stop offset="0" stop-color="#1b6fc4"/>
          <stop offset="1" stop-color="#1f3fae"/>
        </linearGradient>
      </defs>
      <path d="M40 260 Q170 190 200 0 L200 260 Z" fill="url(#sweepFront)"/>
    </svg>
  </section>

  <section class="card card--back">
    <div class="brand-dot"></div>
    <div class="wordmark">nimbora</div>
    <div class="lot-photo" role="img" aria-label="Photo of rows of parked cars in an open city parking lot"></div>
    <svg class="corner-sweep" width="200" height="260" viewBox="0 0 200 260">
      <defs>
        <linearGradient id="sweepBack" x1="0" y1="0" x2="0" y2="1">
          <stop offset="0" stop-color="#1b6fc4"/>
          <stop offset="1" stop-color="#1f3fae"/>
        </linearGradient>
      </defs>
      <path d="M40 260 Q170 190 200 0 L200 260 Z" fill="url(#sweepBack)"/>
    </svg>
    <p class="back-url">www.website.com</p>
  </section>
</body>
</html>
```